Volbrey Inc Business Card

Looking to get an updated business card for a Contract Machining company (www.volbreyinc.example) - looking for a clean design the portrays the technical nature of the business - colors can follow the website design and be in any combination that makes sense (red black, white, metallic or silver) - logos attached for use also. Would like space for: Name, title, business phone (555 214-3086), cell phone , website (www.volbreyinc.example) - possibly QR code could be integrated for website (designer choice), business address - 418 Harlow Bend, Frankenmuth, MI 48199 (cards will be for 4 employees, I will either need to modify a template or I can provide individual information)
Target Market(s)
Aerospace, defense and medical device manufacturing companies that need machining
Industry/Entity Type
Machining for aerospace, defense, medical
Contact Information for Business Card
Name, Title, Business Phone, Cell Phone, email, business website and business address
Look and feel

```html
<!DOCTYPE html>
<html lang="en">
<head>
<meta charset="utf-8">
<title>Volbrey Inc Business Card</title>
<link href="https://fonts.googleapis.com/css2?family=Montserrat:wght@800&family=Poppins:wght@400;500&display=swap" rel="stylesheet">
<style>
  :root {
    --red: #b21e23;
    --black: #0b0b0b;
    --white: #ffffff;
    --ink: #1c1c1c;
    --grey-soft: #d9d9d9;
    --stage: #2a2a2a;
  }
  * { margin: 0; padding: 0; box-sizing: border-box; }
  html, body { width: 1200px; height: 866px; overflow: hidden; }
  body {
    background: var(--stage);
    display: flex;
    flex-direction: column;
    align-items: center;
    justify-content: center;
    gap: 40px;
    font-family: "Poppins", sans-serif;
  }
  .card {
    position: relative;
    width: 640px;
    height: 366px;
    overflow: hidden;
    box-shadow: 0 10px 30px rgba(0,0,0,.45);
  }

  /* Front */
  .card-front { background: var(--white); color: var(--ink); }
  .front-texture {
    position: absolute; left: 0; top: 0;
    width: 340px; height: 170px;
    background: linear-gradient(135deg, var(--grey-soft) 0%, rgba(255,255,255,0) 70%);
  }
  .holder { position: absolute; left: 32px; top: 118px; }
  .holder-name {
    font-family: "Montserrat", sans-serif; font-weight: 800;
    font-size: 23px; letter-spacing: 1px; color: var(--red);
  }
  .holder-title { font-size: 15px; margin-top: 2px; }
  .divider {
    position: absolute; left: 32px; right: 28px; top: 206px;
    height: 1px; background: var(--ink);
  }
  .contacts { position: absolute; left: 32px; top: 220px; list-style: none; font-size: 14px; line-height: 24px; }
  .contacts li { display: flex; align-items: center; gap: 10px; }
  .contacts svg { width: 14px; height: 14px; fill: var(--red); flex: none; }
  .brand-mark {
    position: absolute; right: 40px; top: 28px;
    width: 130px; height: 130px; border-radius: 50%; background: var(--red);
  }
  .brand-name {
    position: absolute; right: 40px; top: 164px;
    font-family: "Montserrat", sans-serif; font-weight: 800;
    font-size: 28px; letter-spacing: 1px; color: var(--red);
  }
  .address {
    position: absolute; right: 28px; top: 222px;
    text-align: right; font-size: 14px; line-height: 22px;
  }
  .footer-band { position: absolute; left: 0; bottom: 0; width: 640px; height: 40px; }
  .website {
    position: absolute; right: 28px; bottom: 8px;
    color: var(--white); font-size: 14px; font-weight: 500; letter-spacing: .5px;
  }

  /* Back */
  .card-back {
    background: var(--black);
    display: flex; align-items: center; justify-content: center;
  }
  .back-texture {
    position: absolute; inset: 0;
    background: radial-gradient(ellipse at 35% 45%, #262626 0%, var(--black) 65%);
  }
  .back-brand {
    position: relative;
    font-family: "Montserrat", sans-serif; font-weight: 800;
    font-size: 64px; letter-spacing: 2px; color: var(--red);
  }
</style>
</head>
<body>

  <section class="card card-front">
    <div class="front-texture" role="img" aria-label="Faint grey brand symbol decoration"></div>

    <div class="holder">
      <p class="holder-name">MARCUS HALE</p>
      <p class="holder-title">Managing Director</p>
    </div>

    <div class="divider"></div>

    <ul class="contacts">
      <li>
        <svg viewBox="0 0 24 24" aria-hidden="true"><path d="M6.6 10.8a15.1 15.1 0 0 0 6.6 6.6l2.2-2.2a1 1 0 0 1 1-.25 11.4 11.4 0 0 0 3.6.57 1 1 0 0 1 1 1V20a1 1 0 0 1-1 1A17 17 0 0 1 3 4a1 1 0 0 1 1-1h3.5a1 1 0 0 1 1 1c0 1.25.2 2.45.57 3.57a1 1 0 0 1-.25 1z"/></svg>
        555 214-3086
      </li>
      <li>
        <svg viewBox="0 0 24 24" aria-hidden="true"><path d="M7 1h10a2 2 0 0 1 2 2v18a2 2 0 0 1-2 2H7a2 2 0 0 1-2-2V3a2 2 0 0 1 2-2zm0 3v14h10V4zm5 15.5a1 1 0 1 0 0 2 1 1 0 0 0 0-2z"/></svg>
        555 867-4412
      </li>
      <li>
        <svg viewBox="0 0 24 24" aria-hidden="true"><path d="M2 5h20v14H2zm2 2v.5l8 5 8-5V7l-8 5z"/></svg>
        info@volbreyinc.example
      </li>
    </ul>

    <div class="brand-mark"></div>
    <p class="brand-name">VOLBREY</p>

    <address class="address" style="font-style: normal;">
      418 Harlow Bend,<br>Frankenmuth, MI 48199
    </address>

    <svg class="footer-band" viewBox="0 0 640 40" aria-hidden="true">
      <rect x="0" y="30" width="330" height="5" fill="var(--red)"/>
      <path d="M300 40 C 330 40, 330 6, 365 6 L 640 6 L 640 40 Z" fill="var(--black)"/>
    </svg>
    <p class="website">www.volbreyinc.example</p>
  </section>

  <section class="card card-back">
    <div class="back-texture" role="img" aria-label="Dark brand symbol decoration"></div>
    <p class="back-brand">VOLBREY</p>
  </section>

</body>
</html>
```